Quote Cards With KB May 2025 for Instagram

I would like to put these quotes over one of the pictures attached; Instagram (new size: 4:5 (1080 x 1350 pixels) One Quote per picture, and I want the quote to be bold or easy to read as well. I provided a few reference graphics that I really like as examples below. In very small letters at the bottom add @KBHarlowOnline

All of the pictures are attached; you can pick any photo and add one quote to it; but no stock photography

```html
<!DOCTYPE html>
<html lang="en">
<head>
<meta charset="utf-8">
<title>KB Quote Cards – May 2025</title>
<link rel="stylesheet" href="https://fonts.googleapis.com/css2?family=Oswald:wght@400;500;600;700&family=Exo+2:wght@600;700&family=Roboto:wght@700&display=swap">
<style>
  :root {
    --board: #6b6b6b;
    --board-dark: #3e3e3e;
    --magenta: #ff0784;
    --magenta-deep: #cc0066;
    --magenta-top: #f0268a;
    --hot-pink: #ff0080;
    --blush: #f5dff0;
    --ink: #232323;
    --white: #ffffff;
  }
  * { margin: 0; padding: 0; box-sizing: border-box; }
  html, body { width: 1200px; height: 3892px; overflow: hidden; }
  body {
    background: radial-gradient(ellipse at center, var(--board-dark) 0%, var(--board-dark) 45%, var(--board) 100%);
    position: relative;
  }
  .card {
    position: absolute;
    left: 134px;
    width: 931px;
    height: 1164px;
    overflow: hidden;
    box-shadow: 0 20px 60px rgba(0,0,0,.55);
  }
  .card svg.deco { position: absolute; inset: 0; width: 100%; height: 100%; }
  .handle {
    position: absolute;
    left: 0; right: 0;
    top: 1060px;
    text-align: center;
    font: 700 27px/1 "Roboto", sans-serif;
  }

  /* Card 1 */
  .card--hormones {
    top: 133px;
    background: linear-gradient(180deg, var(--magenta-top) 0%, var(--magenta-deep) 60%, var(--magenta-deep) 100%);
  }
  .hormones__banner {
    position: absolute;
    left: 65px; top: 287px;
    width: 801px; height: 234px;
    background: var(--white);
    display: flex; flex-direction: column; justify-content: center; align-items: center;
    font: 700 86px/98px "Oswald", sans-serif;
    color: var(--magenta);
    text-transform: uppercase;
    letter-spacing: -1px;
  }
  .hormones__body {
    position: absolute;
    left: 0; right: 0; top: 566px;
    text-align: center;
    font: 500 84px/98px "Oswald", sans-serif;
    color: var(--white);
    text-shadow: 3px 4px 4px rgba(0,0,0,.35);
  }
  .card--hormones .handle { color: var(--white); }

  /* Card 2 */
  .card--fault { top: 1365px; background: var(--white); }
  .fault__title {
    position: absolute;
    left: 116px; top: 238px;
    font: 700 94px/104px "Exo 2", sans-serif;
    color: var(--magenta-deep);
  }
  .fault__tag {
    position: absolute;
    left: 116px; top: 508px;
    width: 698px; height: 95px;
    background: var(--magenta);
    color: var(--white);
    font: 700 72px/95px "Exo 2", sans-serif;
    text-align: center;
  }
  .fault__body {
    position: absolute;
    left: 116px; top: 648px;
    font: 600 51px/75px "Exo 2", sans-serif;
    color: var(--ink);
  }
  .card--fault .handle { color: var(--ink); }

  /* Card 3 */
  .card--tummy { top: 2596px; background: var(--blush); }
  .tummy__title {
    position: absolute;
    left: 0; width: 840px; top: 72px;
    text-align: center;
    font: 700 122px/128px "Oswald", sans-serif;
    text-transform: uppercase;
    color: var(--ink);
    letter-spacing: -2px;
  }
  .tummy__title span { color: var(--hot-pink); display: block; }
  .tummy__body {
    position: absolute;
    left: 0; right: 0; top: 580px;
    text-align: center;
    font: 400 78px/102px "Oswald", sans-serif;
    color: var(--white);
    letter-spacing: -1.5px;
    text-shadow: 3px 4px 4px rgba(0,0,0,.3);
  }
  .card--tummy .handle { color: var(--white); }
</style>
</head>
<body>

<section class="card card--hormones">
  <svg class="deco" viewBox="0 0 931 1164" aria-hidden="true">
    <circle cx="-180" cy="-150" r="720" fill="#ffffff" opacity=".07"/>
    <circle cx="1010" cy="1330" r="580" fill="#ffffff" opacity=".1"/>
    <circle cx="853" cy="85" r="113" fill="#ffffff" opacity=".25"/>
    <circle cx="853" cy="85" r="56" fill="#ffffff" opacity=".35"/>
    <circle cx="82" cy="1099" r="113" fill="#ffffff" opacity=".25"/>
    <circle cx="82" cy="1099" r="56" fill="#ffffff" opacity=".35"/>
  </svg>
  <h2 class="hormones__banner"><span>Tired. Moody.</span><span>Stubborn belly fat.</span></h2>
  <p class="hormones__body">Your hormones are<br>screaming for help!<br>Let’s fix that.</p>
  <p class="handle">@KBHarlowOnline</p>
</section>

<section class="card card--fault">
  <svg class="deco" viewBox="0 0 931 1164" aria-hidden="true">
    <polygon points="0,0 195,0 213,73 0,131" fill="#cc0066"/>
    <polygon points="704,1002 931,941 931,1164 750,1164" fill="#ff0784"/>
  </svg>
  <h2 class="fault__title">THAT STUBBORN<br>WEIGHT?</h2>
  <p class="fault__tag">It’s not your fault.</p>
  <p class="fault__body">Your hormones are to blame<br>and you’re not alone;<br>But there is a fix.</p>
  <p class="handle">@KBHarlowOnline</p>
</section>

<section class="card card--tummy">
  <svg class="deco" viewBox="0 0 931 1164" aria-hidden="true">
    <polygon points="0,574 931,260 931,1164 0,1164" fill="#ff0784"/>
    <polygon points="541,390 705,555 931,331 931,260" fill="#ff2a95"/>
  </svg>
  <h2 class="tummy__title">Flat tummy in<span>your 40s?</span></h2>
  <p class="tummy__body">It’s still possible!<br>Comment BYE BELLY<br>to get the 10 secrets to<br>a flatter tummy</p>
  <p class="handle">@KBHarlowOnline</p>
</section>

</body>
</html>
```